Flyer Design Project for Sports Medicine Services

I am a sports medicine doctor specialising in the diagnosis and management of sport and exercise injuries for all ages and levels of activity - from elite to weekend jogger. I work under the Business name Peak Stride Athletics and do have a company logo. I am wanting a flier that I can send to family doctors, physiotherapists and sports clubs explaining who I am what I can offer and why they should send me patients.
- I have a Masters in Sports Medicine (MSportsMed), Diplomas in Obstetrics/Gynaecology (DRANZCOG) and also Paediatrics (DCH) and certificate in advanced clinical hypnosis
-accurate diagnosis and management plan with their regular physio to return the player / athlete to the field / court /gym as soon as safely possible
-hypnosis for sports performance eg anxiety control, confidence and mental rehearsal for individuals and teams
- because there are many possible therapists and therapy options, as a sports doctor I can work out who they need to see a physiotherapist, surgeon, massage therapist chiropractor or podiatrist to return them to activity or whether cortisone, PRP or autologous blood injections are needed
-can provide one point of contact for coaches and clubs for rehabilitation and return to sport advice.
- work with Laura Pemberton ex Australian Athlete, a Performance Strategist (NLB listed resource person) and registered Psychologist for best mental preparation for individuals teams and coach development
- can organise rapid access to MRI, ultrasound and specialist appointments if needed
-I work at 3 practices KinetaCare 518 Hollis Rd Hollis 84619027 Monday Wednesday Friday; Brackley Sports Clinic, 193 Brackley Rd, Adelaide 81946372 Tuesday Riverton Hawks Sports Medicine Clinic, Tolvane Arena 8162 5907 Thursday.
-facebook site peakstrideathletics
Updates
Hi All, just to clarify.. My name is Simon Drewett and I am the sports doctor. My wife is Laura Pemberton and she is the psychologist. The flier should mainly be advertising my sports medicine services and a byline ( or at least not the first line in the title) about the Performance Strategy and Coach development.
Target Market(s)
family doctors (GPs), Sporting Clubs, Physiotherapists
Industry/Entity Type
Massage
Look and feel

```html
<!DOCTYPE html>
<html lang="en">
<head>
<meta charset="utf-8">
<title>Dr. Simon Drewett – Sports Medicine Flyer</title>
<link rel="stylesheet" href="https://fonts.googleapis.com/css2?family=Arimo:ital,wght@0,400;0,700;1,400;1,700&display=swap">
<style>
  :root {
    --cyan: #5cc6ea;
    --cyan-deep: #2ba9d8;
    --lime: #9bd13a;
    --ink: #141414;
    --paper: #ffffff;
    --panel: rgba(255, 255, 255, 0.78);
    --photo-light: #b8ab96;
    --photo-mid: #6f6454;
    --photo-dark: #3b342c;
    --xray: #4a6690;
    --page: #d9dcdc;
  }
  * { box-sizing: border-box; margin: 0; padding: 0; }
  html, body {
    width: 1200px; height: 800px; overflow: hidden;
    background: var(--page);
    font-family: "Arimo", Arial, sans-serif;
    color: var(--ink);
  }
  .flyer {
    position: relative;
    width: 1200px; height: 800px;
    overflow: hidden;
    background: var(--paper);
  }
  .flyer-shapes { position: absolute; inset: 0; }

  .brand {
    position: absolute; left: 20px; top: 44px; width: 175px;
    text-align: center;
  }
  .brand-mark {
    display: block; width: 58px; height: 58px; margin: 0 auto 14px;
    border-radius: 50%; background: var(--cyan);
  }
  .brand-name {
    font-size: 19px; font-weight: 700; line-height: 1.15;
    color: var(--cyan-deep);
  }
  .brand-address {
    margin-top: 32px;
    font-size: 13px; line-height: 1.45;
  }

  .locations {
    position: absolute; left: 22px; top: 447px;
    font-size: 17px; line-height: 22px;
  }
  .location + .location { margin-top: 22px; }

  .web {
    position: absolute; left: 295px; top: 768px;
    font-size: 13px;
  }

  .doctor-name {
    position: absolute; left: 244px; top: 46px;
    font-size: 39px; font-weight: 700; font-style: italic;
    color: var(--paper);
    letter-spacing: 0.5px;
    text-shadow: 3px 3px 5px rgba(0,0,0,0.7);
  }

  .info-panel {
    position: absolute; left: 672px; top: 82px;
    width: 495px; height: 663px;
    background: var(--panel);
    padding: 30px 21px 12px 21px;
  }
  .info-frame {
    height: 621px;
    border: 4px solid var(--lime);
    padding: 4px 14px 0 12px;
  }
  .tagline {
    font-size: 19px; font-weight: 700; font-style: italic;
    line-height: 23px;
  }
  .section-title {
    margin-top: 30px;
    font-size: 16px; font-style: italic; font-weight: 700;
    color: var(--cyan);
    line-height: 20px;
  }
  .section-title.offers { margin-top: 30px; }
  .points { list-style: none; font-size: 16px; line-height: 22px; }
  .points li { padding-left: 10px; text-indent: -10px; }
  .points li::before { content: "•"; display: inline-block; width: 10px; text-indent: 0; }
</style>
</head>
<body>
<main class="flyer">
  <svg class="flyer-shapes" width="1200" height="800" viewBox="0 0 1200 800" aria-hidden="false">
    <defs>
      <linearGradient id="photoTone" x1="0" y1="0" x2="1" y2="1">
        <stop offset="0" stop-color="var(--photo-light)"/>
        <stop offset="0.45" stop-color="var(--photo-mid)"/>
        <stop offset="1" stop-color="var(--photo-dark)"/>
      </linearGradient>
      <linearGradient id="xrayTone" x1="0" y1="0" x2="0" y2="1">
        <stop offset="0" stop-color="#6d88ad"/>
        <stop offset="1" stop-color="var(--xray)"/>
      </linearGradient>
    </defs>
    <g role="img" aria-label="Photograph of the doctor smiling, wearing a stethoscope, in front of lit X-ray films">
      <rect x="0" y="0" width="1200" height="800" fill="url(#photoTone)"/>
      <rect x="760" y="50" width="440" height="600" fill="url(#xrayTone)" opacity="0.55"/>
    </g>
    <path class="side-panel" d="M0 0 H195 C235 260 330 560 577 800 H0 Z" fill="var(--paper)"/>
    <path class="side-curve" d="M195 0 C235 260 330 560 577 800" fill="none" stroke="var(--cyan)" stroke-width="9"/>
    <rect class="frame" x="4" y="4" width="1192" height="792" fill="none" stroke="var(--cyan)" stroke-width="8"/>
    <rect class="frame-inner" x="12" y="12" width="1176" height="776" fill="none" stroke="var(--paper)" stroke-width="4" opacity="0.6"/>
  </svg>

  <header class="brand">
    <span class="brand-mark"></span>
    <p class="brand-name">Peak Stride Athletics</p>
    <p class="brand-address">Calder Heights, Adelaide,<br>South Australia 5091</p>
  </header>

  <section class="locations">
    <div class="location">KinetaCare<br>518 Hollis Rd Hollis<br>84619027<br>Monday Wednesday Friday</div>
    <div class="location">Brackley Sports Clinic<br>193 Brackley Rd, Adelaide<br>81946372<br>Tuesday</div>
    <div class="location">Riverton Hawks Sports Medicine Clinic<br>Tolvane Arena<br>8162 5907<br>Thursday</div>
  </section>

  <p class="web">www.peakstrideathletics.com</p>

  <h1 class="doctor-name">DR. SIMON DREWETT</h1>

  <section class="info-panel">
    <div class="info-frame">
      <p class="tagline">Sports medicine doctor specialising in diagnosis and management of sport and exercise injuries.</p>

      <h2 class="section-title">Background:</h2>
      <ul class="points">
        <li>Masters in Sports Medicine (MSportsMed)</li>
        <li>Fellow of the Southern College of General Practitioners</li>
        <li>Diplomas in Obstetrics/Gynaecology (DRANZCOG) and Paediatrics (DCH)</li>
        <li>Advanced Certificate in Clinical Hypnosis</li>
        <li>Works with Laura Pemberton, a registered psychologist for best mental preparation for individuals, teams and coach development.</li>
      </ul>

      <h2 class="section-title offers">Offers...</h2>
      <ul class="points">
        <li>Accurate diagnosis and management plan with their regular physio to return the player / athlete to the field / court /gym safely as soon as possible.</li>
        <li>Hypnosis for sports performance. eg anxiety control, confidence and mental rehearsal for individuals and teams.</li>
        <li>Recommendation for one point of contact for coaches and clubs for rehabilitation and return to sport advice.</li>
        <li>Organizing rapid access to MRI, ultrasound and specialist appointments if needed.</li>
      </ul>
    </div>
  </section>
</main>
</body>
</html>
```